Silverpath Coverage Guides, LLC
Business cards, letterhead, envelopes, and mailing labels (3.43" x 1.93")
Dale K. Whitcombe
Licensed Insurance Agent
Post Office Box 417 Destin, FL 32817
dale@mysilverpathcg.com
Appointed with all major insurers - Brightwell Carecorp - NSEL Velora Kestrel Wellness Group Pinecrest Assurance and Harbor Ridge Life Wellstep Advantage Pro Lindqvist Silverpath Coverage Guides, LLC Helping find the best plan for your needs!

```html
<!DOCTYPE html>
<html lang="en">
<head>
<meta charset="utf-8">
<title>Silverpath Coverage Guides, LLC — Business Card</title>
<link rel="stylesheet" href="https://fonts.googleapis.com/css2?family=Tinos&family=PT+Sans:ital,wght@1,700&display=swap">
<style>
  :root {
    --page-bg: #e6e7ea;
    --card-bg: #ffffff;
    --brand-blue: #1f6cc4;
    --band-blue: #1d6fd0;
    --brand-green: #27c42a;
    --agent-green: #33b52c;
    --ink: #4a4a4a;
    --rule: #b9b9b9;
    --icon: #6c7f99;
  }
  * { margin: 0; padding: 0; box-sizing: border-box; }
  html, body {
    width: 1200px; height: 780px; overflow: hidden;
    background: var(--page-bg);
  }
  .business-card {
    position: absolute; left: 80px; top: 97px;
    width: 1040px; height: 585px;
    background: var(--card-bg);
    border-radius: 34px;
    overflow: hidden;
    box-shadow: 0 6px 24px rgba(0,0,0,.12);
  }
  .brand { position: absolute; left: 84px; top: 106px; display: flex; align-items: center; gap: 26px; }
  .brand-mark { width: 96px; height: 96px; background: var(--brand-blue); }
  .brand-name {
    font-family: "Tinos", serif; font-size: 44px; color: var(--brand-blue);
    white-space: nowrap;
  }
  .agent {
    position: absolute; right: 510px; top: 246px; text-align: right;
    font-family: "PT Sans", sans-serif; font-style: italic; font-weight: 700;
  }
  .agent-name { font-size: 31px; color: var(--brand-blue); line-height: 1.2; }
  .agent-title { font-size: 22px; color: var(--agent-green); line-height: 1.3; }
  .mailing-address {
    position: absolute; right: 510px; top: 318px; text-align: right;
    font-family: "Tinos", serif; font-size: 23px; color: var(--ink); line-height: 1.35;
  }
  .divider {
    position: absolute; left: 548px; top: 236px; width: 1px; height: 160px;
    background: var(--rule);
  }
  .contact-list {
    position: absolute; left: 562px; top: 236px; list-style: none;
    font-family: "Tinos", serif; font-size: 23px; color: var(--ink);
  }
  .contact-list li { display: flex; align-items: center; gap: 12px; height: 32px; }
  .contact-list svg { width: 20px; height: 20px; flex: none; }
  .swoosh { position: absolute; left: 0; top: 0; width: 1040px; height: 585px; }
</style>
</head>
<body>
  <main class="business-card">
    <svg class="swoosh" viewBox="0 0 1040 585" aria-hidden="true">
      <path d="M0 530 C 300 560, 700 520, 1040 420 L1040 585 L0 585 Z" fill="var(--band-blue)"/>
      <path d="M0 498 C 320 520, 720 470, 1040 392" fill="none" stroke="var(--brand-green)" stroke-width="7"/>
      <path d="M0 512 C 320 540, 720 500, 1040 408" fill="none" stroke="#ffffff" stroke-width="8"/>
    </svg>

    <header class="brand">
      <span class="brand-mark"></span>
      <span class="brand-name">Silverpath Coverage Guides, LLC</span>
    </header>

    <section class="agent">
      <p class="agent-name">Dale K. Whitcombe</p>
      <p class="agent-title">Licensed Insurance Agent</p>
    </section>

    <address class="mailing-address" style="font-style:normal">
      Post Office Box 417<br>Destin, FL 32817
    </address>

    <div class="divider"></div>

    <ul class="contact-list">
      <li>
        <svg viewBox="0 0 20 20"><path d="M5 2 L8 2 L9 6 L7 8 C8 11 9 12 12 13 L14 11 L18 12 L18 15 C18 17 16 18 14 18 C8 17 3 12 2 6 C2 4 3 2 5 2 Z" fill="var(--icon)"/></svg>
        <span>8885550147 (T)</span>
      </li>
      <li>
        <svg viewBox="0 0 20 20"><rect x="5" y="1" width="10" height="18" rx="2" fill="var(--icon)"/><rect x="7" y="4" width="6" height="9" fill="#fff"/></svg>
        <span>8505550362</span>
      </li>
      <li>
        <svg viewBox="0 0 20 20"><rect x="5" y="2" width="10" height="6" fill="var(--icon)"/><rect x="2" y="8" width="16" height="9" rx="1" fill="var(--icon)"/><rect x="6" y="11" width="8" height="2" fill="#fff"/></svg>
        <span>8775550918</span>
      </li>
      <li>
        <svg viewBox="0 0 20 20"><circle cx="10" cy="10" r="8" fill="none" stroke="var(--icon)" stroke-width="2.2"/><circle cx="10" cy="10" r="3" fill="none" stroke="var(--icon)" stroke-width="2.2"/></svg>
        <span>dale@mysilverpathcg.com</span>
      </li>
      <li>
        <svg viewBox="0 0 20 20"><circle cx="10" cy="10" r="8" fill="var(--icon)"/><path d="M2 10 H18 M10 2 C6 6 6 14 10 18 M10 2 C14 6 14 14 10 18" fill="none" stroke="#fff" stroke-width="1.2"/></svg>
        <span>mysilverpathcg.com</span>
      </li>
    </ul>
  </main>
</body>
</html>
```